Snapnook needs You

Help us create an inviting, amazing, sleek, simple, clear landing page for a picture-memory-social connection site!

Business Name: SnapNook
Industry: Social Networking and Creativity through Pictures
A web platform for and about a community that is driven by a passion for sharing, caring, bonding, collaborating, creating and earning with pictures, through pictures and other related creative activities. This is going to be a great site for all creative artists-photographers, artists, graphic artists to express their work and their creativity.

The main focus of the site is - CONNECTIONS.
This will be uncoded.

Desired Website Screen Size
1024x768... Widescreen/Landscape orientation, is what we mean... So it fits on a CPU screen.

Desired look and feel and message
Look: Visitor should feel immersed in the page, in the world the page creates, simple, elegant, sophisticated, contemporary. We really like a clean uncluttered look.

Special mention: By the way we love the marketing genius who thought up this branding for velu yogurt where they used the two dots above the o to create a branding effect that made this brand instantly identifiable. http://www.velu-dairy.ca/en/

The two dots by themselves without having even the name present brings up the whole brand now. The dots are used above all the ingredients of the yogurt creating friendly figures, and above people in commercials-bringing the people onto the side of "team" velu. Snapnook may have a character created or something distinctive in the letters in the name created to brand the site as well.

Feel: Engaging; Magical without being corny, here is a link to give an example look and feel but please do not be hindered in your creativity by this suggestion. We love all creative angles.
http://artscrapyard.com/graphic/5829317-camera-film-roll-blue-background

Message: Life and memories and connections through pictures.

Target audience:
The site is focused on pictures but not confined to photography enthusiasts (although they are an integral part of the site). Customers/Visitors will include families, corporates and the younger generation - all age groups, all class, everyone with pictures to express, memories to share.

Website design we like:
http://brindlework.com/work/northern-ballet-house/
http://brindlework.com/work/zapverse/

What colors do we want to see on our landing page?
We would like the background to be grey or blue since it is grey is picture neutral colour and blue highlights pictures well and we also like blue and silver, which can be integrated into the theme. Also like green. But please do not let these instructions limit your creativity. We are open to new ideas and colours.

Predetermined Concepts if any:
We have a concept in mind and we think it would be cool to have an interface for the user through the back of a camera on the landing page -This could be used to create a scene or world the visitor feels a part of or is immersed into. The back screen of the camera may act as a screen for the slideshow of featured pictures on the site.

Content on the Page:
Photo Gallery with full screen, thumbnail view, zoom option etc.
Prominent but short introductory message
Sign in / Login Options
Links: Home Page; About; Info/Help; Contact Us; Privacy Policy; Terms of Use
At the bottom of the page: Follow Me/Like/Workplaza...social buttons.

Please feel free to add any other element to the landing page that you think might add to the effect of simple yet amazing look -clean, simple, uncluttered, sophisticated, stylish, inviting and engaging.
The concept is a guideline, but we would like you to be as creative as you can, even if it meant stepping out of these guidelines - rethink design, style, content if you like. We believe in bringing a solution in an innovative yet simple and elegant style. Something a visitor would be intrigued enough to explore and the guest would feel comfortable enough taking that step forward to have fun on the site. If you believe in the same, and you have the skill then you will have what we need. Good luck, go for it and we are excited to see what the amazing designers on this amazing site have to offer.
If you have any questions please free to ask.

HI wanted to send an update that this project design has been guaranteed.

Our site will be one to celebrate and showcase imagination as well as connection.  We would love to see what you create. Keep in mind our site will showcase all creativity, photographs, artists, graphic artists so this would be a benefit you may want to take advantage of in the future, a place where, if you so choose, you could gain exposure for your work. Therefore, even if you do not win the design project there is possible future benefit.

Imagination is everything.
Imagination encircles the world.-Halvorsen

Reason: We are giving the designers who accepted invites but have not yet submitted a chance to finish their submissions and the ones who are working on revisions a chance to finish those:)

Hello everyone,

Due to time constraints we must come to a decision sooner than the deadline of 28th. 

So, please try to submit any new designs or modifications to the old ones before the 26th. We are very thankful to all of you who have participated - for your designs, enthusiasm and kind words. 

Good luck! :)

• Thank you for the interest shown and your submissions! Designers who have submitted up until now have shown great potential. We are VERY excited with the quality of work and designs.

We want to add that Snapnook is not exclusively for the photographers. The site is for every person who may have a picture to store, organise, use or share - whether publicly or with only a few friends and family.

Snapnook is about allowing people to take control of their creativity. It is about providing tools to our users so that they can build their own connections and social network... of friends, family, fans, clients, ideas, thoughts, emotions etc. through pictures without worrying about their privacy or control over their creations.

With this update we want to encourage others to go beyond the camera theme. Do not let us restrict your creativity. Let YOUR OWN ideas take over if that’s what you think will best convey the message and will appeal to the users.

```html
<!DOCTYPE html>
<html lang="en">
<head>
<meta charset="utf-8">
<title>SnapNook</title>
<link href="https://fonts.googleapis.com/css2?family=Arimo:wght@400;700&family=Nunito:wght@800&family=Kalam&display=swap" rel="stylesheet">
<style>
:root{
  --bg:#0c0c0c;
  --bg-glow:#2a2a2a;
  --panel:#2b2b2b;
  --panel-edge:#444;
  --panel-inner:#232323;
  --thumb-frame:#0e0e0e;
  --text:#e6e6e6;
  --text-soft:#b5b5b5;
  --text-dim:#8a8a8a;
  --accent:#2fb0e0;
  --accent-dark:#1a8cc0;
  --grey-btn:#5a5a5a;
  --grey-btn-dark:#3a3a3a;
  --bar:#1d1d1d;
}
*{margin:0;padding:0;box-sizing:border-box}
html,body{width:1200px;height:939px;overflow:hidden}
body{
  position:relative;
  background:
    radial-gradient(ellipse 420px 360px at 300px 620px, var(--bg-glow), transparent 75%),
    var(--bg);
  font-family:"Arimo",Arial,sans-serif;
  color:var(--text);
}
.abs{position:absolute}
.brand{left:92px;top:36px;font-family:"Nunito",sans-serif;font-weight:800;font-size:58px;color:#e4e4e4;letter-spacing:-1px}
.account-bar{left:616px;top:46px;width:495px;height:44px;background:linear-gradient(90deg,transparent,var(--bar) 30%);display:flex;justify-content:flex-end;align-items:center;padding-right:20px;font-size:13px;gap:14px;color:var(--text)}
.account-bar a{color:var(--text);text-decoration:none}
.side-nav{left:92px;top:122px;height:271px;border-left:2px solid #3a3a3a;width:170px}
.side-nav a{position:absolute;left:22px;font-size:13px;color:var(--text-soft);text-decoration:none}
.side-nav .current{left:2px;width:157px;height:24px;top:14px;background:#1e1e1e;padding-left:20px;line-height:24px;color:var(--text)}
.side-nav .current::before{content:"";position:absolute;left:0;top:6px;border-left:7px solid #555;border-top:6px solid transparent;border-bottom:6px solid transparent}
.gallery{left:298px;top:131px;width:813px;height:287px;background:var(--panel);border:4px solid var(--panel-edge);box-shadow:inset 0 0 0 3px var(--panel-inner)}
.thumb{position:absolute;width:92px;height:74px;border:3px solid var(--thumb-frame);background:linear-gradient(135deg,#9a9a9a,#3c3c3c)}
.thumb.dark{background:linear-gradient(135deg,#555,#111)}
.thumb.light{background:linear-gradient(135deg,#d8d8d8,#7a7a7a)}
.thumb.green{background:linear-gradient(135deg,#7d9a2e,#2f4612)}
.tooltip{left:353px;top:246px;width:170px;height:34px;background:#161616;border:1px solid #3a3a3a;border-radius:3px;font-size:12px;color:var(--text-soft);padding:9px 0 0 18px}
.tooltip::before{content:"";position:absolute;left:72px;top:-7px;border-bottom:7px solid #3a3a3a;border-left:7px solid transparent;border-right:7px solid transparent}
.pager{width:48px;height:48px;border-radius:50%;background:linear-gradient(#3e3e3e,#262626);border:1px solid #444}
.intro{left:643px;top:440px;width:468px}
.intro h1{font-weight:400;font-size:25px;color:#f2f2f2;margin-left:3px}
.intro p{margin-top:18px;font-size:12px;line-height:23px;color:var(--text-soft);text-align:justify}
.btn{height:55px;width:221px;border-radius:3px;display:flex;align-items:center;justify-content:center;gap:12px;font-size:23px;font-weight:700;color:#fff;letter-spacing:.5px}
.btn-signin{left:643px;top:589px;background:linear-gradient(var(--accent),var(--accent-dark))}
.btn-register{left:884px;top:589px;background:linear-gradient(var(--grey-btn),var(--grey-btn-dark))}
.btn svg{width:18px;height:18px}
.tagline{left:647px;top:672px;width:464px;display:flex;justify-content:space-between;font-family:"Kalam",cursive;font-size:18px;color:#6c6c6c}
.featured{left:643px;top:718px;width:468px;height:153px;background:#252525}
.featured h2{position:absolute;left:22px;top:16px;font-weight:400;font-size:17px;color:var(--accent);width:190px;padding-bottom:12px;border-bottom:1px solid #555}
.featured .meta{position:absolute;left:22px;top:68px;font-size:12px;line-height:23px;color:var(--text-soft)}
.featured .more{position:absolute;left:23px;top:121px;font-size:12px;color:var(--accent);text-decoration:underline;display:flex;gap:10px;align-items:center}
.featured .photo{position:absolute;left:222px;top:7px;width:238px;height:141px;border:3px solid #111;background:linear-gradient(#b49a44,#6a5a28 45%,#2a3020)}
.footer{left:0;top:911px;width:1200px;text-align:center;font-size:12px;color:var(--text-dim)}
</style>
</head>
<body>
<div class="abs brand">SnapNook</div>
<nav class="abs account-bar"><a href="#">LOG IN</a><span>|</span><a href="#">LOG OUT</a></nav>

<nav class="abs side-nav">
  <a class="current" href="#">HOME</a>
  <a href="#" style="top:55px">ABOUT US</a>
  <a href="#" style="top:97px">CONTACT US</a>
  <a href="#" style="top:138px">HELP</a>
  <a href="#" style="top:180px">PRIVACY POLICY</a>
  <a href="#" style="top:222px">TERMS OF USE</a>
</nav>

<section class="abs gallery" aria-label="Photo gallery">
  <div class="thumb green" role="img" aria-label="Hand touching a glass bottle on grass" style="left:60px;top:19px"></div>
  <div class="thumb dark" role="img" aria-label="Dark splash photo" style="left:178px;top:19px"></div>
  <div class="thumb light" role="img" aria-label="Black and white portrait photo" style="left:296px;top:19px"></div>
  <div class="thumb light" role="img" aria-label="Figure leaping over water" style="left:415px;top:19px"></div>
  <div class="thumb" role="img" aria-label="Black and white portrait photo" style="left:533px;top:19px"></div>
  <div class="thumb light" role="img" aria-label="Bare branches in fog" style="left:651px;top:19px"></div>
  <div class="thumb dark" role="img" aria-label="Bokeh lights photo" style="left:60px;top:105px"></div>
  <div class="thumb light" role="img" aria-label="Trees in winter" style="left:178px;top:105px"></div>
  <div class="thumb light" role="img" aria-label="Bird in flight" style="left:296px;top:105px"></div>
  <div class="thumb" role="img" aria-label="Black and white portrait photo" style="left:415px;top:105px"></div>
  <div class="thumb light" role="img" aria-label="Bird on a branch" style="left:651px;top:105px"></div>
  <div class="thumb dark" role="img" aria-label="Figure in smoke" style="left:60px;top:190px"></div>
  <div class="thumb light" role="img" aria-label="Two birds" style="left:178px;top:190px"></div>
  <div class="thumb light" role="img" aria-label="Hands forming a sign" style="left:296px;top:190px"></div>
  <div class="thumb" role="img" aria-label="Camera on a strap" style="left:415px;top:190px"></div>
  <div class="thumb light" role="img" aria-label="Heart shape in snow" style="left:533px;top:190px"></div>
  <div class="thumb dark" role="img" aria-label="Narrow street at night" style="left:651px;top:190px"></div>
</section>

<div class="abs pager" style="left:302px;top:242px">
  <svg width="48" height="48" viewBox="0 0 48 48"><path d="M28 15 L18 24 L28 33 Z" fill="#111"/></svg>
</div>
<div class="abs pager" style="left:1059px;top:242px">
  <svg width="48" height="48" viewBox="0 0 48 48"><path d="M20 15 L30 24 L20 33 Z" fill="#2d7fd0"/></svg>
</div>
<div class="abs tooltip">Bottle by&nbsp; Marten Hale</div>

<section class="abs intro">
  <h1>Welcome to our site</h1>
  <p>At vero eos et accusamus et iusto odio dignissimos ducimus qui blanditiis praesentium voluptatum deleniti atque corrupti quos dolores et quas molestias excepturi sint occaecati cupiditate non provident, similique sunt in culpa qui officia.</p>
</section>

<a class="abs btn btn-signin" href="#">SIGN IN
  <svg viewBox="0 0 18 18"><circle cx="9" cy="9" r="8" fill="#222"/><path d="M5 9h6M9 6l3 3-3 3" stroke="#fff" stroke-width="1.8" fill="none"/></svg>
</a>
<a class="abs btn btn-register" href="#">REGISTER
  <svg viewBox="0 0 18 18"><circle cx="9" cy="9" r="8" fill="#222"/><path d="M5 9h6M9 6l3 3-3 3" stroke="#fff" stroke-width="1.8" fill="none"/></svg>
</a>

<div class="abs tagline"><span>join with us....</span><span>Meet New People....</span><span>Share New things</span></div>

<section class="abs featured">
  <h2>FEATURED PICTURE</h2>
  <div class="meta">Photo by : Marten Hale<br>Category : Surf</div>
  <a class="more" href="#">View all Photos
    <svg width="16" height="10" viewBox="0 0 16 10"><path d="M0 5h10M1 2h6M1 8h6M9 1l5 4-5 4" stroke="#2fb0e0" stroke-width="2" fill="none"/></svg>
  </a>
  <div class="photo" role="img" aria-label="Surfer riding a wave at sunset"></div>
</section>

<footer class="abs footer">Copyright © 2012 www.snapnook.com&nbsp;&nbsp;&nbsp; All rights reserved.</footer>
</body>
</html>
```